Label design - Superfood blend

We are a family owned nutrition company with big ambitions. Our goal is to develop a range of 100% natural supplements for women, inspired by nature & modern technology that helps them meet their nutritional needs while nourishing them from within. All our products are junk free because we believe that that’s how nature intended it. We also produce products through a sustainable process and only use biodegradable packaging for our products (See link - https://www.loamwrap.org.uk/biodegradable-stand-pouch-250g-kraft)

Our brand style is modern and minimalist. This same style will be reflected in our social media, website and we want it to be represented through the label designs for our product packaging.

We want some creative designers to design a label that is true to our style (See attached packaging brief with designs we like) and displays our values of Premium, High Quality, Organic Real Food supplements focused on women. I have provided examples in the attached brief, but please only use as inspiration, I dont want any of them to be copied (sorry have had my fingers burnt already !)
Updates

Hello all, Please note this design is for a LABEL and not the whole package. We will have a 500gm biodegradable brown package, and we will have a label (which is what this project is about) that will be stuck on the front. The size of the label will be a rectangle (unless you come up with a new shape) in the size 20cm * 15cm. Please do not submit designs for the WHOLE from of the package, as we dont intend to have printed packages. Regards

Hello all, I have added a new logo version to the attachments, could you please also try that version. Could you also please look at the new sliders. We are only looking for a minimlaist theme. If you dont know what that means, please do feel free to ask, I would be happy to supply examples. Minimalist designs, means clean, modern, upmarket, elegant designs. It does not use too many colors and mostly sticks to a combination of black and white with colors used sparingly. See some below for your reference anyway. https://www.pitchloft.co.uk/design/13359317 https://www.pitchloft.co.uk/design/17270649 https://www.pitchloft.co.uk/design/12584145 https://www.pitchloft.co.uk/design/12367479 https://www.snapquilt.com/search/pins/?q=minimalist%20label%20design&rs=rs&eq=&etslf=2809&term_meta[]=minimalist%7Crecentsearch%7Cundefined&term_meta[]=label%7Crecentsearch%7Cundefined&term_meta[]=design%7Crecentsearch%7Cundefined Regards

Target Market(s)

The target market is women between the age 25 to 45, based in UK (mostly based in larger cities in UK). They are typically middle class or higher and would be in demanding jobs and social lives, that requires for them to meet their nutrition needs in convenient, easy to take forms. The women would also be socially conscious and sensitive to issues like women's rights, environmental issues, healthy food, organic food and sustainability etc. I have a much more detailed customer avatar if required

Font styles to use
Serif
Sans Serif
Decorative
Script

Colors
e8e8e8
474747
1b1b1b
add136

Requirements
Must have
• The label, should look minimalist and modern, throw in some out of the box creativity and we have a winner. Creativity will definitely be of importance. Our packaging is a biodegradable brown paper stand up pouch (Example link in product description). So to make it standout from other colorful packaging - being creative would definitely help.
• Please use the color schemes provided in the brief (See attachments). But if you want to experiment I would be open to it, as long as they are still minimalist and does not stray very far from the color given in the brief :)

```html
<!DOCTYPE html>
<html lang="en">
<head>
<meta charset="utf-8">
<title>Verdale – Tend The Gut label range</title>
<link rel="stylesheet" href="https://fonts.googleapis.com/css2?family=Montserrat:wght@300;400;600&display=swap">
<style>
  :root {
    --canvas: #f2f2f2;
    --label: #ffffff;
    --ink: #1b1b1b;
    --ink-soft: #474747;
    --rule: #e8e8e8;
    --muted: #9a9a9a;
    --lime: #add136;
  }
  * { box-sizing: border-box; margin: 0; padding: 0; }
  html, body { width: 1200px; height: 857px; overflow: hidden; }
  body {
    background: var(--canvas);
    font-family: "Montserrat", sans-serif;
    color: var(--ink-soft);
    position: relative;
  }
  .label-range {
    position: absolute;
    left: 0; top: 295px;
    width: 1200px; height: 266px;
  }
  .label {
    position: absolute;
    top: 0;
    width: 196px; height: 266px;
    background: var(--label);
    border-radius: 10px;
    overflow: hidden;
    box-shadow: 0 1px 3px rgba(0,0,0,.08);
  }
  .label:nth-child(1) { left: 97px; }
  .label:nth-child(2) { left: 365px; }
  .label:nth-child(3) { left: 634px; }
  .label:nth-child(4) { left: 903px; }

  .brand-name {
    position: absolute;
    left: 31px; top: 135px;
    transform: translate(-50%, -50%) rotate(-90deg);
    font-weight: 400;
    font-size: 19px;
    letter-spacing: 9px;
    color: var(--ink);
    white-space: nowrap;
  }
  .brand-dot {
    display: inline-block;
    width: 6px; height: 6px;
    border-radius: 50%;
    background: var(--lime);
    margin-right: 8px;
    vertical-align: middle;
  }

  .product-title {
    position: absolute;
    left: 56px; top: 102px;
    width: 124px;
    padding: 3px 5px 4px;
    background: var(--ink-soft);
    color: #fff;
  }
  .product-title h1 {
    font-weight: 600;
    font-size: 13px;
    letter-spacing: .2px;
    line-height: 17px;
    white-space: nowrap;
  }
  .product-title p {
    font-size: 4px;
    letter-spacing: 0;
    white-space: nowrap;
    text-transform: uppercase;
  }
  .label--framed .product-title::after {
    content: "";
    position: absolute;
    left: -4px; top: -4px; right: 6px; bottom: 4px;
    border: 1px solid var(--lime);
  }
  .label--lime .product-title { background: var(--lime); color: var(--ink); }

  .ingredients {
    position: absolute;
    left: 56px; top: 147px;
    width: 124px;
    font-size: 6px;
    font-weight: 300;
    color: var(--ink-soft);
  }
  .ingredients li {
    list-style: none;
    display: flex;
    justify-content: space-between;
    padding: 3px 0;
    border-top: 1px solid var(--rule);
    white-space: nowrap;
  }
  .ingredients .fade { color: var(--muted); }
  .label--lime .ingredients li { border: 0; justify-content: flex-start; gap: 4px; padding: 2px 0; }
  .label--lime .ingredients span {
    background: var(--ink-soft);
    color: #fff;
    padding: 1px 2px;
  }
  .label--lime .ingredients span.fade { background: #8a8a8a; }

  .certifications {
    position: absolute;
    left: 100px; top: 190px;
    display: flex; align-items: center; gap: 18px;
  }
  .cert-seal {
    width: 28px; height: 28px;
    border-radius: 50%;
    border: 1.5px solid var(--ink-soft);
  }
  .cert-mark {
    width: 26px; height: 20px;
    border-radius: 4px;
    border: 1.5px solid var(--lime);
  }

  .net-weight {
    position: absolute;
    right: 12px; bottom: 12px;
    text-align: right;
    font-size: 5px;
    line-height: 6px;
    color: var(--muted);
  }
  .net-weight b {
    display: block;
    margin-top: 1px;
    padding: 1px 4px;
    font-weight: 400;
    background: var(--lime);
    color: #fff;
  }
  .label--lime .net-weight b { background: none; border: 1px solid var(--ink-soft); color: var(--ink-soft); }
  .baseline {
    position: absolute;
    left: 12px; right: 12px; bottom: 31px;
    height: 1px;
    background: var(--muted);
  }

  .corner-weight {
    position: absolute;
    left: 0; bottom: 0;
    width: 52px; height: 52px;
  }
  .corner-weight span {
    position: absolute;
    left: 10px; bottom: 8px;
    font-size: 5px;
    line-height: 6px;
    color: var(--ink-soft);
  }
</style>
</head>
<body>
  <main class="label-range">

    <article class="label label--corner">
      <div class="brand-name"><span class="brand-dot"></span>VERDALE</div>
      <header class="product-title">
        <h1>TEND THE GUT</h1>
        <p>Organic prebiotics and superfood blend</p>
      </header>
      <ul class="ingredients">
        <li><span>Baobab</span>•<span>Flaxseed</span>•<span>Maca</span>•<span class="fade">Acai</span></li>
        <li><span>Goji Berry</span>•<span>Aronia</span>•<span class="fade">Cinnamon</span></li>
      </ul>
      <div class="certifications">
        <div class="cert-seal" role="img" aria-label="Organic certification seal"></div>
        <div class="cert-mark" role="img" aria-label="Vegan certification mark"></div>
      </div>
      <svg class="corner-weight" viewBox="0 0 52 52" aria-hidden="true">
        <polygon points="0,0 52,52 0,52" fill="#add136"/>
      </svg>
      <div class="corner-weight"><span>Weight<br>500 g</span></div>
    </article>

    <article class="label label--framed">
      <div class="brand-name"><span class="brand-dot"></span>VERDALE</div>
      <header class="product-title">
        <h1>TEND THE GUT</h1>
        <p>Organic prebiotics and superfood blend</p>
      </header>
      <ul class="ingredients">
        <li><span>Baobab</span>•<span>Flaxseed</span>•<span>Maca</span>•<span class="fade">Acai</span></li>
        <li><span>Goji Berry</span>•<span>Aronia</span>•<span class="fade">Cinnamon</span></li>
      </ul>
      <div class="certifications">
        <div class="cert-seal" role="img" aria-label="Organic certification seal"></div>
        <div class="cert-mark" role="img" aria-label="Vegan certification mark"></div>
      </div>
      <div class="net-weight">Net Weight<b>500 g</b></div>
    </article>

    <article class="label label--lime">
      <div class="brand-name"><span class="brand-dot"></span>VERDALE</div>
      <header class="product-title">
        <h1>TEND THE GUT</h1>
        <p>Organic prebiotics and superfood blend</p>
      </header>
      <ul class="ingredients">
        <li><span>Baobab</span><span>Flaxseed</span><span>Maca</span><span class="fade">Acai</span></li>
        <li><span>Goji Berry</span><span>Aronia</span><span class="fade">Cinnamon</span></li>
      </ul>
      <div class="certifications">
        <div class="cert-seal" role="img" aria-label="Organic certification seal"></div>
        <div class="cert-mark" role="img" aria-label="Vegan certification mark"></div>
      </div>
      <div class="baseline"></div>
      <div class="net-weight">Net Weight<b>500 g</b></div>
    </article>

    <article class="label">
      <div class="brand-name"><span class="brand-dot"></span>VERDALE</div>
      <header class="product-title">
        <h1>TEND THE GUT</h1>
        <p>Organic prebiotics and superfood blend</p>
      </header>
      <ul class="ingredients">
        <li><span>Baobab</span>•<span>Flaxseed</span>•<span>Maca</span>•<span class="fade">Acai</span></li>
        <li><span>Goji Berry</span>•<span>Aronia</span>•<span class="fade">Cinnamon</span></li>
      </ul>
      <div class="certifications">
        <div class="cert-seal" role="img" aria-label="Organic certification seal"></div>
        <div class="cert-mark" role="img" aria-label="Vegan certification mark"></div>
      </div>
      <div class="net-weight">Net Weight<b>500 g</b></div>
    </article>

  </main>
</body>
</html>
```